Contemporary new French wine brand needs logo and series of label design

to design a new contemporary logo and series of labels for a new French wine brand. We hope to attract not just current French wine drinkers but new ones who may appreciate a less traditional and more modern style.
Updates

Reason: we are wanting to extend the project for a few days more to receive more submissions since we had fewer designs submitted than we were expecting, maybe because of the holidays.

Target Market(s)

people who follow the arts community (eg. music, theatre, visual/video arts, dance) --- all mature ages.

Industry/Entity Type

French Wine

Requirements
Must have
• a clear, memorable treatment for the name MORIVAL with accompanying logo.
Nice to have
• embossing, matte/gloss refinement, tasteful foil stamping, coated stock for the whites to help the integrity of the paper in and out of ice buckets. A combo of say, three types of fonts; a semi custom font for the brand name Morival and maybe a script and one other.
Should not have
• not traditional French

```html
<!DOCTYPE html>
<html lang="en">
<head>
<meta charset="utf-8">
<title>Morival — Wine Label Series</title>
<link href="https://fonts.googleapis.com/css2?family=Ubuntu:wght@400;500;700&display=swap" rel="stylesheet">
<style>
  :root {
    --paper: #ffffff;
    --plum: #4b2534;
    --gold: #c9b37c;
  }
  html, body {
    margin: 0;
    padding: 0;
    overflow: hidden;
    background: var(--paper);
  }
  .sheet {
    position: relative;
    width: 849px;
    height: 1200px;
    background: var(--paper);
    overflow: hidden;
    font-family: "Ubuntu", sans-serif;
  }
  .label {
    position: absolute;
    left: 0;
    width: 849px;
    height: 367px;
  }
  .label--red { top: 85px; color: var(--plum); }
  .label--white { top: 672px; color: var(--gold); }

  .label__bar {
    position: absolute;
    left: 219px;
    top: 0;
    width: 14px;
    height: 367px;
    background: currentColor;
  }
  .label__mark {
    position: absolute;
    left: 401px;
    top: 72px;
    width: 48px;
    height: 48px;
    background: currentColor;
  }
  .label__brand {
    position: absolute;
    left: 0;
    width: 849px;
    top: 150px;
    margin: 0;
    text-align center;
    text-align: center;
    font-weight: 500;
    font-size: 56px;
    line-height: 1;
    letter-spacing: 1px;
    text-transform: lowercase;
    color: currentColor;
  }
  .label__variety {
    position: absolute;
    left: 0;
    width: 849px;
    top: 289px;
    margin: 0;
    text-align: center;
    font-weight: 400;
    font-size: 28px;
    line-height: 1;
    letter-spacing: 0.5px;
  }
  .label__vintage {
    position: absolute;
    left: 0;
    width: 849px;
    top: 330px;
    margin: 0;
    text-align: center;
    font-weight: 700;
    font-size: 15px;
    line-height: 1;
    letter-spacing: 1px;
  }
</style>
</head>
<body>
  <main class="sheet">
    <section class="label label--red">
      <div class="label__bar"></div>
      <div class="label__mark" aria-hidden="true"></div>
      <h1 class="label__brand">Morival</h1>
      <p class="label__variety">CABERNET FRANC</p>
      <p class="label__vintage">2011</p>
    </section>

    <section class="label label--white">
      <div class="label__bar"></div>
      <div class="label__mark" aria-hidden="true"></div>
      <h2 class="label__brand">Morival</h2>
      <p class="label__variety">SAUVIGNON BLANC</p>
      <p class="label__vintage">2011</p>
    </section>
  </main>
</body>
</html>
```